Construction company business card

One side to be the logo with the company name, The other side I would like: (Tomas verbick) Project manager 41 barrow crescent hallam 52917306224783(03) 9703 2428Info@gudeljgroup.comAnd then maybe a couple dot points saying what we do:Construction (commercial & industrial) Civil construction

Anything else please contact me!
Maybe curved st one edge of the card

Target Market(s)

Older clientele

Industry/Entity Type

Construction Company

Contact Information for Business Card

Read above

Colors
3277b5
1b1b1b
9d9d9d

Requirements
Must have
• Use my logo on one side
Nice to have
• Read above
Should not have
• Read above

```html
<!DOCTYPE html>
<html lang="en">
<head>
<meta charset="utf-8">
<title>Stonevale Construction – Business Card</title>
<link href="https://fonts.googleapis.com/css2?family=Open+Sans:ital,wght@0,300;0,400;0,700;1,300&display=swap" rel="stylesheet">
<style>
  :root {
    --page-bg: #ebebeb;
    --card-white: #ffffff;
    --card-dark: #1f1e1f;
    --brand-blue: #3158a6;
    --text-light: #ffffff;
    --text-muted: #e6e6e6;
  }
  * { margin: 0; padding: 0; box-sizing: border-box; }
  html, body {
    width: 1200px; height: 800px; overflow: hidden;
    background: var(--page-bg);
    font-family: "Open Sans", Arial, sans-serif;
  }
  .card {
    position: absolute;
    left: 316px;
    width: 570px; height: 330px;
    background: var(--card-white);
    overflow: hidden;
  }
  .card--front { top: 50px; border-bottom: 2px solid var(--brand-blue); }
  .card--back { top: 419px; }

  .brand {
    position: absolute;
    display: flex; flex-direction: column; align-items: center;
    color: var(--brand-blue);
    font-weight: 700;
    text-align: center;
  }
  .brand__dot {
    width: 78px; height: 78px; border-radius: 50%;
    background: var(--brand-blue);
    margin-bottom: 16px;
  }
  .brand__name { font-size: 34px; line-height: 1; letter-spacing: 1px; }
  .brand__sub { font-size: 15px; letter-spacing: 9px; margin-top: 6px; }

  .card--front .brand { left: 0; right: 0; top: 82px; }

  .card--back .brand { left: 365px; width: 190px; top: 104px; }
  .card--back .brand__dot { width: 54px; height: 54px; margin-bottom: 12px; }
  .card--back .brand__name { font-size: 22px; }
  .card--back .brand__sub { font-size: 10px; letter-spacing: 5px; margin-top: 4px; }

  .card__curve { position: absolute; inset: 0; width: 570px; height: 330px; }

  .contact {
    position: absolute; left: 26px; top: 62px;
    color: var(--text-light);
  }
  .contact__name { font-size: 24px; font-weight: 700; line-height: 1.15; }
  .contact__role { font-size: 16px; font-weight: 300; font-style: italic; color: var(--text-muted); margin-top: 2px; }
  .contact__address { font-size: 13.5px; line-height: 17px; margin-top: 13px; }
  .contact__lines { list-style: none; margin-top: 16px; }
  .contact__lines li {
    display: flex; align-items: center; gap: 9px;
    font-size: 13.5px; line-height: 21px;
  }
  .contact__lines svg { width: 10px; height: 10px; fill: var(--text-light); }
  .services { list-style: none; margin-top: 16px; }
  .services li {
    position: relative; padding-left: 11px;
    font-size: 12px; line-height: 19px;
  }
  .services li::before {
    content: ""; position: absolute; left: 0; top: 8px;
    width: 4px; height: 4px; border-radius: 50%;
    background: var(--brand-blue);
  }
</style>
</head>
<body>

<section class="card card--front">
  <div class="brand">
    <span class="brand__dot"></span>
    <span class="brand__name">STONEVALE</span>
    <span class="brand__sub">CONSTRUCTION</span>
  </div>
</section>

<section class="card card--back">
  <svg class="card__curve" viewBox="0 0 570 330" aria-hidden="true">
    <path d="M0 0 H302 C302 160 338 262 426 330 H0 Z" fill="var(--brand-blue)"/>
    <path d="M0 0 H289 C289 156 322 262 423 330 H0 Z" fill="var(--card-white)"/>
    <path d="M0 0 H284 C284 154 318 262 421 330 H0 Z" fill="var(--card-dark)"/>
  </svg>

  <div class="contact">
    <h1 class="contact__name">Tomas verbick</h1>
    <p class="contact__role">Project manager</p>
    <p class="contact__address">41 barrow crescent hallam<br>52917306224783</p>
    <ul class="contact__lines">
      <li>
        <svg viewBox="0 0 10 10"><path d="M2 0.5 L3.6 2.6 L2.7 3.6 C3.3 5 4.9 6.7 6.4 7.3 L7.4 6.4 L9.5 8 L8.4 9.5 C4.5 9.2 0.8 5.5 0.5 1.6 Z"/></svg>
        (03) 9418 6573
      </li>
      <li>
        <svg viewBox="0 0 10 10"><path d="M0.5 1.8 H9.5 V8.2 H0.5 Z M1.4 2.6 V7.4 H8.6 V2.6 L5 5.2 Z" fill-rule="evenodd"/></svg>
        Info@verbickgroup.com
      </li>
      <li>
        <svg viewBox="0 0 10 10"><circle cx="5" cy="5" r="4.5"/><path d="M2.5 2.5 L4.5 3.5 L4 5.5 L2.2 5 Z M5.8 6 L7.6 6.4 L6.6 8.4 L5.5 7.5 Z" fill="var(--card-dark)"/></svg>
        www.verbickgroup.com
      </li>
    </ul>
    <ul class="services">
      <li>Civil construction</li>
      <li>Construction (commercial &amp; industrial)</li>
    </ul>
  </div>

  <div class="brand">
    <span class="brand__dot"></span>
    <span class="brand__name">STONEVALE</span>
    <span class="brand__sub">CONSTRUCTION</span>
  </div>
</section>

</body>
</html>
```